Marketing Webpage to Sell to Doctors

We need a page design made to improve a marketing site that signs doctors up for a marketing program. Based on the existing site design, we need a new version created to improve the credibility of the solution and include screenshots of the product.

Target Market(s)

Doctors

Industry/Entity Type

Health And Wellness

Number of Pages Required

1 page

Requirements
Must have
• This is the page to redesign: https://www.carepathnow.com/doctor-marketing/add-listing
• Use screenshots attached as well as two profile picture from one of these profiles. Use one with before and after photos.
• http://www.carepathnow.com/gordon-t-waverly-md-dmd
• http://www.carepathnow.com/rafael-c-ornelo-md
Nice to have
• The style can stay as it is, and add in 5 screenshots. one with b&a pictures, general profile, dashboard, lead view to showcase the actual product the doctor is buying.

```html
<!DOCTYPE html>
<html lang="en">
<head>
<meta charset="utf-8">
<title>CarePathNow – Add Your Doctor Listing</title>
<link href="https://fonts.googleapis.com/css2?family=Arimo:wght@400;700&display=swap" rel="stylesheet">
<style>
:root{
  --maroon:#7a1f2e;
  --maroon-dark:#5e1521;
  --page:#ece6e7;
  --band:#e3d3d6;
  --white:#ffffff;
  --ink:#333333;
  --muted:#777777;
  --line:#d9cfd1;
  --field:#f7f4f4;
}
*{box-sizing:border-box;margin:0;padding:0}
html,body{width:861px;height:1200px;overflow:hidden}
body{font-family:"Arimo",Arial,sans-serif;color:var(--ink);background:linear-gradient(#f6f2f3 0,var(--page) 300px,var(--page) 100%);font-size:8px;position:relative}
.wrap{width:642px;margin:0 auto;position:relative}
.topbar{height:46px;display:flex;align-items:center;justify-content:space-between}
.brand{display:flex;align-items:center;gap:6px;font-size:19px;font-weight:700;color:var(--maroon)}
.brand i{width:10px;height:10px;background:var(--maroon);display:block}
.utility{display:flex;gap:14px;color:var(--muted);font-size:8px}
.utility span::before{content:"";display:inline-block;width:6px;height:6px;border-radius:50%;background:#b9a3a7;margin-right:4px;vertical-align:middle}
.mainnav{height:17px;background:var(--maroon);display:flex;justify-content:space-around;align-items:center;font-size:7px;font-weight:700;color:var(--white);letter-spacing:.3px;padding:0 8px}
.mainnav .active{background:var(--white);color:var(--maroon);padding:4px 10px;align-self:flex-end}
.crumbs{height:10px;margin-top:8px;background:#ddd3d5;font-size:6px;color:var(--muted);padding:2px 6px}
.panel{background:var(--white);border:1px solid var(--line)}
.signup{margin-top:14px;height:164px;padding:14px 18px}
.signup h2{font-size:12px;color:var(--maroon)}
.signup h2 a{font-size:8px;color:var(--muted);text-decoration:underline;font-weight:400;margin-left:4px}
.signup h3{font-size:12px;color:var(--ink);margin:3px 0 10px}
.signup h3 b{color:var(--maroon)}
.fields{display:grid;grid-template-columns:repeat(3,1fr);gap:6px 14px}
.fields label{font-size:7px;color:var(--muted)}
.fields label em{color:var(--maroon);font-style:normal}
.fields .box{height:15px;border:1px solid var(--line);background:var(--field);margin-top:2px}
.submit{height:17px;margin-top:11px;background:var(--maroon);color:var(--white);font-weight:700;font-size:8px;display:flex;align-items:center;justify-content:center;letter-spacing:.5px}
.doctor{display:grid;grid-template-columns:1fr 222px;gap:14px;margin-top:16px}
.doctor .info{padding:14px}
.doctor h4{font-size:12px;color:var(--maroon)}
.doctor .role{font-size:8px;color:var(--muted);margin:3px 0 10px}
.media{display:grid;grid-template-columns:170px 1fr;gap:10px}
.video{height:140px;background:linear-gradient(135deg,#6d6f73,#a59a8f);position:relative}
.video svg{position:absolute;left:72px;top:56px}
.practice{font-size:9px;font-weight:700;line-height:1.35}
.blurb{font-size:7px;line-height:1.55;color:var(--muted);margin-top:6px}
.ba{padding:14px}
.ba h5{font-size:11px;color:var(--maroon)}
.ba .by{font-size:6.5px;color:var(--muted);margin:3px 0 8px}
.pair{display:grid;grid-template-columns:1fr 1fr;gap:4px}
.pair div{height:68px;background:linear-gradient(160deg,#dcb9a4,#c49483)}
.ba .proc{font-size:7.5px;font-weight:700;margin-top:7px}
.ba .more{display:flex;justify-content:space-between;font-size:7px;color:var(--maroon);margin-top:4px}
.dots{display:flex;gap:3px;align-items:center}
.dots i{width:4px;height:4px;border-radius:50%;background:#c9b9bc;display:block}
.dots i:first-child{background:var(--maroon)}
.d1{height:196px}.d2{height:218px}
.showcase{display:grid;grid-template-columns:1fr 200px;gap:20px;margin-top:16px;height:260px}
.shots{position:relative}
.shot{position:absolute;background:linear-gradient(#f4f6f9,#dde5ee);border:1px solid #c8cfd8;box-shadow:0 2px 6px rgba(0,0,0,.18)}
.s1{left:20px;top:60px;width:140px;height:130px}
.s2{left:110px;top:20px;width:180px;height:170px;background:linear-gradient(#ffffff,#e5ebf2)}
.s3{left:250px;top:50px;width:150px;height:140px}
.s4{left:70px;top:150px;width:120px;height:80px}
.s5{left:260px;top:150px;width:130px;height:80px}
.pitch{padding-top:40px}
.pitch h6{font-size:14px;color:var(--maroon);margin-bottom:8px}
.pitch p{font-size:7.5px;line-height:1.6;color:var(--muted)}
.footer{position:absolute;left:0;right:0;top:1048px}
.tab{width:60px;height:14px;background:var(--band);margin-left:110px;font-size:7px;color:var(--maroon);font-weight:700;text-align:center;padding-top:3px}
.footband{height:72px;background:var(--band)}
.footband .wrap{display:flex;justify-content:space-between;align-items:center;height:100%}
.footlinks{display:flex;gap:36px;font-size:7.5px;color:var(--ink)}
.social{display:flex;gap:6px;align-items:center;font-size:7px;color:var(--muted)}
.social i{width:14px;height:14px;border-radius:50%;background:#b79da2;display:block}
.legal{padding-top:8px;font-size:6px;color:var(--muted);line-height:1.6}
.legal .links{color:var(--maroon)}
</style>
</head>
<body>
<div class="wrap">
  <header class="topbar">
    <div class="brand"><i></i>CarePathNow.com</div>
    <nav class="utility"><span>Home</span><span>Blog</span><span>Newsletter Signup</span><span>Doctor Reviews</span></nav>
  </header>
  <nav class="mainnav">
    <span>FIND A DOCTOR</span><span>ASK A DOCTOR</span><span>BEFORE AND AFTER GALLERY</span><span>RESOURCES</span><span>FINANCING</span><span class="active">DOCTORS ONLY</span>
  </nav>
  <div class="crumbs">Home &gt; Doctors Only &gt; Add Listing</div>

  <section class="panel signup">
    <h2>Already an Advertiser? <a>Click here</a></h2>
    <h3>Or Start Your <b>FREE Doctor</b> Listing Now</h3>
    <div class="fields">
      <label>First name <em>*</em><div class="box"></div></label>
      <label>Last name <em>*</em><div class="box"></div></label>
      <label>Practice name <em>*</em><div class="box"></div></label>
      <label>Specialty <em>*</em><div class="box"></div></label>
      <label>Email <em>*</em><div class="box"></div></label>
      <label>Zip <em>*</em><div class="box"></div></label>
      <label>State <em>*</em><div class="box"></div></label>
      <label>Country <em>*</em><div class="box"></div></label>
      <div class="submit">SUBMIT</div>
    </div>
  </section>

  <section class="doctor">
    <div class="panel info d1">
      <h4>Gordon T. Waverly, M.D., D.M.D.</h4>
      <p class="role">Double Board Certified Plastic Surgeon</p>
      <div class="media">
        <div class="video" role="img" aria-label="Video still of the surgeon in his office">
          <svg width="24" height="24" viewBox="0 0 24 24"><circle cx="12" cy="12" r="11" fill="rgba(255,255,255,.8)"/><path d="M9 7l8 5-8 5z" fill="#7a1f2e"/></svg>
        </div>
        <div>
          <p class="practice">Waverly Plastic Surgery<br>– Redefining Youth</p>
          <p class="blurb">Dr. Waverly offers patients a full range of facial and body procedures in a calm private setting. His team guides each visit from the first consult through recovery with clear plans and care that fits every goal.</p>
        </div>
      </div>
    </div>
    <aside class="panel ba d1">
      <h5>Before and After Pictures</h5>
      <p class="by">Performed by Gordon T. Waverly, M.D.</p>
      <div class="pair"><div role="img" aria-label="Before photo of a nose procedure"></div><div role="img" aria-label="After photo of a nose procedure"></div></div>
      <p class="proc">Nose Job (Rhinoplasty)</p>
      <div class="more"><span>View Month »</span><span class="dots"><i></i><i></i><i></i><i></i></span></div>
    </aside>
  </section>

  <section class="doctor">
    <div class="panel info d2">
      <h4>Rafael C. Ornelo, M.D.</h4>
      <p class="role">Cosmetic Treatments and Eye Care Procedures</p>
      <div class="media">
        <div class="video" role="img" aria-label="Video still of the eye surgeon in his clinic">
          <svg width="24" height="24" viewBox="0 0 24 24"><circle cx="12" cy="12" r="11" fill="rgba(255,255,255,.8)"/><path d="M9 7l8 5-8 5z" fill="#7a1f2e"/></svg>
        </div>
        <div>
          <p class="practice">Desert Vista Eye Institute &amp; Cosmetic Laser Center</p>
          <p class="blurb">Dr. Ornelo leads a team of eye surgeons and skin experts who offer vision care and cosmetic laser treatments. Patients can explore options, view results and book a consult with the clinic online.</p>
        </div>
      </div>
    </div>
    <aside class="panel ba d2">
      <h5>Before and After Pictures</h5>
      <p class="by">Performed by Rafael C. Ornelo, M.D.</p>
      <div class="pair"><div role="img" aria-label="Before photo of an eyelid procedure"></div><div role="img" aria-label="After photo of an eyelid procedure"></div></div>
      <p class="proc">Eyelid Lift Surgery (Blepharoplasty)</p>
      <div class="more"><span>View Month »</span><span class="dots"><i></i><i></i><i></i><i></i></span></div>
    </aside>
  </section>

  <section class="showcase">
    <div class="shots">
      <div class="shot s1" role="img" aria-label="Screenshot of a doctor profile page"></div>
      <div class="shot s3" role="img" aria-label="Screenshot of the before and after gallery"></div>
      <div class="shot s2" role="img" aria-label="Screenshot of the doctor dashboard"></div>
      <div class="shot s4" role="img" aria-label="Screenshot of the lead view"></div>
      <div class="shot s5" role="img" aria-label="Screenshot of lead statistics"></div>
    </div>
    <div class="pitch">
      <h6>Lorem Ipsum is simply</h6>
      <p>Lorem ipsum is simply dummy text of the printing and typesetting industry. Lorem ipsum has been the standard dummy text ever since the 1500s, when an unknown printer took a galley of type and scrambled it to make a type specimen book.</p>
    </div>
  </section>
</div>

<footer class="footer">
  <div class="tab">Company</div>
  <div class="footband">
    <div class="wrap">
      <nav class="footlinks"><span>Home</span><span>Find a Doctor</span><span>Before and After Gallery</span><span>Resources</span><span>Financing</span><span>Doctors Blog</span></nav>
      <div class="social">Follow us <i></i><i></i><i></i><i></i></div>
    </div>
  </div>
  <div class="wrap legal">
    <p>Copyright © 2024 CarePathNow. All rights reserved.</p>
    <p>Use of this site is subject to our Terms of Use and Privacy Policy. Content is for general information only and is not medical advice.</p>
    <p class="links">About Us | Privacy Policy | Terms | Site Map | Contact</p>
  </div>
</footer>
</body>
</html>
```